Upstart Retirement Planning Firm needs help with business card design

Harborview Nest Advisors, LLC is looking for help with business card design. We give advice on investments, insurance, and other financial matters related to retirement. There are some required disclosures that we will provide but mostly we are looking for a professional, classy business card that reflects the theme we have chosen. We have a logo that is attached but we would like to add a phrase; "Shaping Your Working Years Into Steady Retirement Pay"

Doubled sided only so that we can add the required disclosures (needed for our industry) on the back of the card. We will provide the exact words for this in 1-2 days.

Target Market(s)

Retirees and Pre-retirees. Professionals 50+ years old

Industry/Entity Type

Financial Planning

Contact Information for Business Card

We currently have two people who will need separate cards so we'd like to have a template so that we can add names for new cards in the future.

For the first run, please show the following information.

Gregor Pelham, MBA, ChFC®, CLU®
Financial Advisor, Registered Representative
gpelham@harborviewnest.example
Phone: (555) 318-2946
Toll Free Fax: (800) 555-0193

Address is
2187 Meadowlark Ridge Rd.
Suite K418
Virginia Beach, VA 23999

Colors
3277b5

Requirements
Must have
• Logo, contact info, small phase to describe business (in description), required legal disclosures on back of the card as follows (in small font)
• Gregor Pelham is a registered representative of and offers securities through Brightmoor Capital Brokerage Corporation, Member FNQX. Brightmoor Capital Brokerage Corporation is a member of the Brightmoor Capital Alliance which is the marketing name for Brightmoor Holding Corporation and its affiliates.
Nice to have
• Rounded edges, raised letters
Should not have
• any colors that aren't in the logo (other than black for font)

```html
<!DOCTYPE html>
<html lang="en">
<head>
<meta charset="utf-8">
<title>Harborview Nest Advisors — Business Cards</title>
<link rel="stylesheet" href="https://fonts.googleapis.com/css2?family=Arimo:wght@400;700&family=Marcellus&display=swap">
<style>
  :root {
    --stage: #e9e6e2;
    --card: #ffffff;
    --ink: #111111;
    --brand-blue: #1f3f99;
    --brand-grey: #8a8f96;
    --shadow: rgba(0, 0, 0, 0.28);
  }
  * { margin: 0; padding: 0; box-sizing: border-box; }
  html, body {
    width: 1200px;
    height: 1000px;
    overflow: hidden;
    background: var(--stage);
  }
  .stage {
    position: relative;
    width: 1200px;
    height: 1000px;
  }
  .card {
    position: absolute;
    width: 571px;
    height: 334px;
    background: var(--card);
    border-radius: 14px;
    box-shadow: 2px 3px 6px var(--shadow);
  }
  .card--front { left: 313px; top: 146px; }
  .card--back-left { left: 17px; top: 507px; }
  .card--back-right { left: 611px; top: 507px; }

  .brand {
    position: absolute;
    left: 0;
    right: 0;
    top: 204px;
    text-align: center;
  }
  .brand__name {
    font-family: "Marcellus", serif;
    font-variant: small-caps;
    font-size: 23px;
    line-height: 28px;
    color: var(--brand-blue);
    letter-spacing: 0.4px;
  }
  .tagline {
    position: absolute;
    left: 0;
    right: 0;
    top: 285px;
    text-align: center;
    font-family: "Marcellus", serif;
    font-variant: small-caps;
    font-size: 16.5px;
    color: var(--ink);
    letter-spacing: -0.1px;
  }

  .contact {
    position: absolute;
    left: 23px;
    right: 17px;
    top: 177px;
    font-family: "Arimo", sans-serif;
    color: var(--ink);
    font-size: 14px;
    line-height: 19px;
  }
  .card--back-right .contact { text-align: right; }
  .contact__name {
    font-weight: 700;
    font-size: 15.5px;
    margin-bottom: 8px;
  }
  .contact__role { margin-bottom: 19px; }
</style>
</head>
<body>
<main class="stage">
  <section class="card card--front" aria-label="Card front">
    <div class="brand">
      <p class="brand__name">Harborview Nest Advisors, LLC</p>
    </div>
    <p class="tagline">Shaping Your Working Years Into Steady Retirement Pay</p>
  </section>

  <section class="card card--back-left" aria-label="Card back, left aligned">
    <div class="contact">
      <p class="contact__name">GREGOR PELHAM</p>
      <div class="contact__role">
        <p>MBA, ChFC®, CLU®</p>
        <p>Financial Advisor, Registered Representative</p>
      </div>
      <p>Email: gpelham@harborviewnest.example</p>
      <p>Phone: (555) 318-2946 &nbsp;|&nbsp; Toll Free Fax: (800) 555-0193</p>
      <p>2187 Meadowlark Ridge Rd., Suite K418, Virginia Beach, VA 23999</p>
    </div>
  </section>

  <section class="card card--back-right" aria-label="Card back, right aligned">
    <div class="contact">
      <p class="contact__name">GREGOR PELHAM</p>
      <div class="contact__role">
        <p>MBA, ChFC®, CLU®</p>
        <p>Financial Advisor, Registered Representative</p>
      </div>
      <p>Email: gpelham@harborviewnest.example</p>
      <p>Phone: (555) 318-2946 &nbsp;|&nbsp; Toll Free Fax: (800) 555-0193</p>
      <p>2187 Meadowlark Ridge Rd., Suite K418, Virginia Beach, VA 23999</p>
    </div>
  </section>
</main>
</body>
</html>
```